Fitness website

Website for a fitness brand (see attached specs). Design needs to be modern and vibrant with CTAs on every page. We will provide logos, images, etc but for now user placeholder text and images. For now use the name 'Corvane Athletics' as the name to use on the design. The goal of this site is to either get people to join the gym (5 physical locations across the US); buy an online program; buy merch or supplements or sign up for the newsletter. Pleas use images from this foldeR: https://filebarn.example/share/folders/8QwTz41mKpLrXv93NdYe7HsaBuJ0Cf2_R?usp=sharing

We will be coding this in ReactNative. Lots more work for the winner as well, this is a 1st project for us.

Target Market(s)

fitness enthusiats

Industry/Entity Type

fitness, health, wellness

Number of Pages Required

5+ page

Font styles to use
Other font styles liked:
• Lato

Colors
0054AA
0677BA
7BADD7
CADEEF
E8F1F8
0094D4
00A9DD
6FCCEA
C7EBF8
E9F6FB
00AB8E
00BBA5
67D7C9
C6EFE9
E9F9F6
EE7325
F08F49
F5BC92
FAE3D3
FDF4ED

Requirements
Must have
• must be reactive. most people will view it first on mobile
Nice to have
• video in hero section of top of home page

```html
<!DOCTYPE html>
<html lang="en">
<head>
<meta charset="utf-8">
<title>Corvane Athletics</title>
<link href="https://fonts.googleapis.com/css2?family=Lato:ital,wght@0,400;0,700;0,900;1,400&family=Josefin+Sans:wght@400;600&display=swap" rel="stylesheet">
<style>
:root{
  --green:#1a7a32;
  --green-dark:#146328;
  --ink:#1a1a1a;
  --dark:#1c1c1c;
  --gray-band:#ececec;
  --white:#ffffff;
  --muted:#cfcfcf;
  --body:#333333;
}
*{box-sizing:border-box;margin:0;padding:0}
html,body{width:1200px;height:4525px;overflow:hidden;background:var(--white)}
body{position:relative;font-family:"Lato",sans-serif;color:var(--ink)}
.abs{position:absolute}
.shape{position:absolute;left:0;top:0}
.btn{position:absolute;display:flex;align-items:center;justify-content:center;border-radius:26px;background:var(--green);color:var(--white);font-family:"Josefin Sans",sans-serif;font-weight:600;font-size:14px;letter-spacing:.3px;text-transform:uppercase}
.btn-dark{background:#111}
.photo{position:absolute}

/* header */
.nav-bar{left:0;top:46px;width:1200px;height:59px;background:rgba(15,15,15,.6)}
.brand{left:74px;top:60px;color:var(--white);font-weight:900;font-size:25px;letter-spacing:.5px}
.nav{left:490px;top:67px;display:flex;gap:34px;font-family:"Josefin Sans",sans-serif;font-size:14px;color:var(--white);font-weight:600}
.nav .active{text-decoration:underline;text-underline-offset:5px}

/* hero */
.hero-title{left:0;width:1200px;top:318px;text-align:center;color:var(--white);font-weight:900;font-size:60px;letter-spacing:1px}
.hero-sub{left:170px;width:860px;top:394px;text-align:center;color:var(--white);font-weight:700;font-size:27px;line-height:36px}

/* section headings */
.h2{position:absolute;font-weight:900;font-size:41px;color:var(--ink);text-transform:uppercase}
.h2-center{left:0;width:1200px;text-align:center}
.rule{position:absolute;height:3px;background:var(--green);width:98px}

/* about */
.about-text{left:617px;width:510px;top:1012px;font-family:"Josefin Sans",sans-serif;font-size:13.5px;line-height:26.5px;color:var(--body)}
.about-text p+p{margin-top:12px}

/* programs */
.program-card{position:absolute;top:1745px;width:292px;height:372px;overflow:hidden}
.program-card .photo{left:0;top:0;width:100%;height:100%}
.program-name{position:absolute;left:0;width:100%;color:var(--white);font-weight:900;font-size:28px;text-align:center;line-height:32px;text-transform:uppercase}
.dots{position:absolute;display:flex;gap:11px}
.dots span{display:block;width:58px;height:3px;background:#555}
.dots span.on{background:#111;height:4px}

/* testimonial */
.quote-mark{left:0;width:1200px;top:2440px;text-align:center;color:#7fbf8d;font-weight:900;font-size:44px;line-height:44px}
.quote{left:170px;width:860px;top:2470px;text-align:center;font-style:italic;font-size:19.5px;line-height:31px;color:var(--body)}
.quote-name{left:0;width:1200px;top:2582px;text-align:center;color:var(--green);font-weight:700;font-size:14px;font-family:"Josefin Sans",sans-serif}

/* locations */
.loc-frame{position:absolute;border:5px solid var(--green);border-top:none}
.loc-label{position:absolute;color:var(--white);font-weight:700;font-size:20px;text-align:center;text-transform:uppercase}

/* blog */
.post-title{position:absolute;font-size:23px;line-height:29px;color:var(--ink);text-transform:uppercase}
.post-date{position:absolute;font-family:"Josefin Sans",sans-serif;font-size:14px;color:var(--green);font-weight:600}

/* footer */
.foot-head{position:absolute;color:var(--white);font-weight:700;font-size:18px;text-transform:uppercase}
.foot-brand{position:absolute;color:var(--white);font-weight:900;font-size:27px}
.foot-text{position:absolute;font-family:"Josefin Sans",sans-serif;color:var(--muted);font-size:14.5px;line-height:26px}
.foot-list{position:absolute;list-style:none;font-family:"Josefin Sans",sans-serif;color:var(--muted);font-size:15px;line-height:37.5px}
.social{position:absolute;top:4335px;left:884px;display:flex;gap:14px}
.social span{width:40px;height:40px;border-radius:50%;background:#3a3a3a;display:block}
.social span.on{background:var(--green)}
.footer-rule{left:0;top:4455px;width:1200px;height:1px;background:#3a3a3a}
.copyright{left:0;width:1200px;top:4483px;text-align:center;font-family:"Josefin Sans",sans-serif;font-size:13px;color:#aaa}
</style>
</head>
<body>

<!-- hero -->
<div class="photo" style="left:0;top:0;width:1200px;height:794px;background:linear-gradient(160deg,#2c3236 0%,#3d4246 40%,#23272a 100%)" role="img" aria-label="Two athletes training with a barbell in a gym"></div>
<svg class="shape" width="1200" height="800" viewBox="0 0 1200 800">
  <polygon points="600,756 1200,700 1200,794" fill="#1a7a32"/>
  <polygon points="0,794 600,756 1200,794" fill="#ffffff"/>
</svg>
<div class="abs nav-bar"></div>
<div class="abs brand">CORVANE ATHLETICS</div>
<nav class="abs nav">
  <span class="active">HOME</span><span>ABOUT US</span><span>PROGRAM</span><span>SHOP</span><span>LOCATION</span>
</nav>
<div class="btn" style="left:970px;top:52px;width:155px;height:45px">Contact Us</div>
<h1 class="abs hero-title">CORVANE ATHLETICS</h1>
<p class="abs hero-sub">Nemo enim ipsam voluptatem quia voluptas sit aspernatur aut odit aut fugit, sed quia consequuntur magni dolores.</p>
<div class="btn" style="left:445px;top:500px;width:152px;height:48px">Learn More</div>
<div class="btn btn-dark" style="left:610px;top:500px;width:152px;height:48px">
  <svg width="14" height="14" viewBox="0 0 14 14" style="margin-right:7px"><circle cx="7" cy="7" r="6" fill="none" stroke="#fff" stroke-width="1.4"/><polygon points="5.5,4.3 9.8,7 5.5,9.7" fill="#fff"/></svg>Play Video
</div>

<!-- about -->
<div class="photo" style="left:0;top:878px;width:589px;height:519px;background:linear-gradient(135deg,#4a4540,#2a2724 60%,#1b1a19);clip-path:polygon(0 0,589px 0,497px 519px,0 519px)" role="img" aria-label="Woman and man lifting barbells in a gym"></div>
<svg class="shape" width="600" height="1400" viewBox="0 0 600 1400" style="pointer-events:none">
  <polygon points="589,1050 589,1397 497,1397" fill="#1a7a32"/>
</svg>
<h2 class="h2" style="left:617px;top:945px">About</h2>
<div class="rule" style="left:780px;top:968px"></div>
<div class="abs about-text">
  <p>Nemo enim ipsam voluptatem quia voluptas sit aspernatur aut odit aut fugit, sed quia consequuntur magni dolores eos qui ratione voluptatem sequi nesciunt. Neque porro quisquam est, qui dolorem ipsum quia dolor sit amet, consectetur, adipisci velit, sed quia non numquam eius modi tempora incidunt ut labore et dolore magnam.</p>
  <p>Nemo enim ipsam voluptatem quia voluptas sit aspernatur aut odit aut fugit, sed quia consequuntur magni dolores eos qui ratione voluptatem sequi nesciunt. Neque porro quisquam est.</p>
</div>
<div class="btn" style="left:617px;top:1271px;width:151px;height:47px">Learn More</div>

<!-- programs -->
<svg class="shape" width="1200" height="2290" viewBox="0 0 1200 2290">
  <polygon points="0,1530 1200,1505 1200,2279 0,2279" fill="#ececec"/>
  <polygon points="0,1483 600,1527 0,1572" fill="#1a7a32"/>
</svg>
<h2 class="h2 h2-center" style="top:1620px">Our Programs</h2>
<div class="rule" style="left:551px;top:1688px"></div>

<div class="program-card" style="left:0">
  <div class="photo" style="background:linear-gradient(180deg,#6a6560,#3a3633 60%,#1d1b1a)" role="img" aria-label="Athlete training on a rowing machine"></div>
  <div class="program-name" style="top:237px">Masters</div>
  <div class="btn" style="left:70px;top:303px;width:150px;height:47px">Learn More</div>
</div>
<div class="program-card" style="left:302px">
  <div class="photo" style="background:linear-gradient(180deg,#7a7670,#44413d 60%,#1f1d1c)" role="img" aria-label="Woman doing battle rope training"></div>
  <div class="program-name" style="top:220px">Functional<br>Fitness</div>
  <div class="btn" style="left:70px;top:303px;width:150px;height:47px">Learn More</div>
</div>
<div class="program-card" style="left:606px">
  <div class="photo" style="background:linear-gradient(180deg,#5c6670,#3a3f44 60%,#1d1e20)" role="img" aria-label="Athlete lifting a loaded barbell in competition"></div>
  <div class="program-name" style="top:237px">Competitive</div>
  <div class="btn" style="left:70px;top:303px;width:150px;height:47px">Learn More</div>
</div>
<div class="program-card" style="left:908px">
  <div class="photo" style="background:linear-gradient(180deg,#5a4a3e,#3c342d 60%,#1e1b18)" role="img" aria-label="Man preparing a healthy meal bowl"></div>
  <div class="program-name" style="top:237px">Nutritions</div>
  <div class="btn" style="left:70px;top:303px;width:150px;height:47px">Learn More</div>
</div>
<div class="dots" style="left:501px;top:2187px"><span class="on"></span><span></span><span></span></div>

<!-- testimonials -->
<h2 class="h2 h2-center" style="top:2332px">Testimonials</h2>
<div class="rule" style="left:551px;top:2400px"></div>
<div class="abs quote-mark">&#8221;</div>
<p class="abs quote">" Nemo enim ipsam voluptatem quia voluptas sit aspernatur aut odit aut fugit, sed quia consequuntur magni dolores eos qui ratione voluptatem sequi nesciunt porro quisquam est, qui dolorem ipsum quia dolor sit amet, consectetur.."</p>
<div class="abs quote-name">NAME HEADING</div>
<div class="dots" style="left:501px;top:2660px"><span class="on"></span><span></span><span></span></div>

<!-- locations -->
<svg class="shape" width="1200" height="3450" viewBox="0 0 1200 3450">
  <defs>
    <linearGradient id="locBg" x1="0" y1="0" x2="1" y2="1">
      <stop offset="0" stop-color="#2a2d30"/><stop offset=".5" stop-color="#3b3e41"/><stop offset="1" stop-color="#1c1e20"/>
    </linearGradient>
  </defs>
  <polygon points="0,2714 1200,2745 1200,3440 0,3425" fill="url(#locBg)" role="img" aria-label="Woman lifting weights in a dark gym"/>
  <polygon points="700,2760 1200,2730 1200,2800" fill="#1a7a32"/>
  <polygon points="0,3350 620,3375 0,3425" fill="#1a7a32"/>
</svg>
<h2 class="h2 h2-center" style="top:2857px;color:#fff">Our Locations</h2>
<div class="rule" style="left:551px;top:2924px"></div>

<div class="loc-frame" style="left:206px;top:2973px;width:252px;height:261px"></div>
<div class="photo" style="left:211px;top:2973px;width:242px;height:256px;background:linear-gradient(180deg,#7fb3de,#9cc3d8 45%,#3f6f55 75%,#2b5b77)" role="img" aria-label="San Diego skyline by the bay"></div>
<div class="loc-frame" style="left:487px;top:2973px;width:235px;height:248px;border-top:5px solid var(--green)"></div>
<div class="photo" style="left:492px;top:2978px;width:225px;height:238px;background:linear-gradient(180deg,#8fbfe6,#b9cfdc 45%,#6d7f8a 65%,#3d7b96)" role="img" aria-label="Boston skyline over the harbor"></div>
<div class="loc-frame" style="left:745px;top:2973px;width:253px;height:261px"></div>
<div class="photo" style="left:750px;top:2973px;width:243px;height:256px;background:linear-gradient(180deg,#3a4a6a,#c87a4a 45%,#4a3a40 70%,#1f2a3a)" role="img" aria-label="Miami skyline at dusk"></div>
<div class="loc-label" style="left:211px;width:242px;top:3250px">San Diego</div>
<div class="loc-label" style="left:487px;width:235px;top:3250px">Boston</div>
<div class="loc-label" style="left:750px;width:243px;top:3250px">Miami</div>
<svg class="shape" width="1200" height="3200" viewBox="0 0 1200 3200" style="pointer-events:none">
  <polyline points="160,3082 142,3100 160,3118" fill="none" stroke="#fff" stroke-width="3"/>
  <polyline points="1045,3082 1063,3100 1045,3118" fill="none" stroke="#fff" stroke-width="3"/>
</svg>

<!-- blog -->
<h2 class="h2" style="left:74px;top:3490px">Blog Posts</h2>
<div class="rule" style="left:74px;top:3560px"></div>
<div class="btn" style="left:975px;top:3510px;width:150px;height:47px">View All</div>

<div class="photo" style="left:74px;top:3604px;width:527px;height:333px;background:linear-gradient(180deg,#3a3c44,#2a2a2e 60%,#151516)" role="img" aria-label="Athletes lifting weight plates overhead"></div>
<div class="post-title" style="left:96px;top:3865px;color:#fff;font-size:22px">NEMO ENIM IPSAM VOLUPTA</div>
<div class="post-date" style="left:96px;top:3898px">OCTOBER 16, 2025</div>

<div class="photo" style="left:615px;top:3604px;width:241px;height:158px;background:linear-gradient(135deg,#5b554e,#2e2a27)" role="img" aria-label="Two athletes training together on the gym floor"></div>
<div class="post-title" style="left:870px;top:3625px">NEMO ENIM IPSAM<br>VOLU PTATEM RATIONE<br>VOLUPTA TEM SEQUI</div>
<div class="post-date" style="left:870px;top:3722px">AUGUST 25, 2025</div>

<div class="photo" style="left:615px;top:3777px;width:241px;height:160px;background:linear-gradient(135deg,#3b3b40,#1d1d20)" role="img" aria-label="Athlete running through an indoor arena"></div>
<div class="post-title" style="left:870px;top:3802px">NEMO ENIM IPSAM<br>VOLU PTATEM RATIONE<br>VOLUPTA TEM SEQUI</div>
<div class="post-date" style="left:870px;top:3899px">AUGUST 25, 2025</div>

<!-- footer -->
<svg class="shape" width="1200" height="4525" viewBox="0 0 1200 4525">
  <polygon points="0,4018 1200,4060 1200,4525 0,4525" fill="#1c1c1c"/>
  <polygon points="700,4072 1200,4040 1200,4112" fill="#1a7a32"/>
</svg>
<div class="foot-brand" style="left:74px;top:4150px">CORVANE ATHLETICS</div>
<p class="foot-text" style="left:74px;top:4200px;width:330px">Excepteur sint occaecat cupidatat non proident, sunt in culpa qui officia deserunt mollit anim id est laborum.</p>
<p class="foot-text" style="left:74px;top:4290px;width:330px">Enim ipsam voluptatem quia voluptas sit aspernatur aut odit aut fugit, sed quia consequuntur magni dolores.</p>

<div class="foot-head" style="left:462px;top:4152px">Navigations</div>
<ul class="foot-list" style="left:462px;top:4185px">
  <li>Home</li><li>About Us</li><li>Program</li><li>Shop</li><li>Location</li>
</ul>
<div class="foot-head" style="left:682px;top:4152px">About Us</div>
<ul class="foot-list" style="left:682px;top:4185px">
  <li>Brands</li><li>Gyms</li><li>Coaches</li><li>Owner</li><li>Athlete Team</li>
</ul>
<div class="foot-head" style="left:884px;top:4152px">Contact Info</div>
<p class="foot-text" style="left:884px;top:4190px;width:260px;line-height:28px">48 Harlow Lane Suite 210,<br>Brookfield 20455, Ohio</p>
<p class="foot-text" style="left:884px;top:4254px">+1-555-010-2288</p>
<p class="foot-text" style="left:884px;top:4282px">info@corvaneathletics.example</p>
<div class="social"><span class="on"></span><span></span><span></span><span></span></div>

<div class="abs footer-rule"></div>
<div class="abs copyright">©2025 Company Name &nbsp;| All Right Reserved &amp; Privacy Policy</div>

</body>
</html>
```